Q&J RESTORATION

I want a brochure similiar to the example i've attached.
My company name is Q&J Restoration. The website is: Q-J-Restoration.example.
The phone number is 919.555.0147.

I don't like the "yellow" being the main color of the example so I'm open to suggestions. I want something CLEAN & Simple, like our logo . This will be a bi fold brochure

```html
<!DOCTYPE html>
<html lang="en">
<head>
<meta charset="utf-8">
<title>Q&amp;J Restoration – Bi-fold Brochure</title>
<link href="https://fonts.googleapis.com/css2?family=Raleway:wght@300;400;500;600;700&display=swap" rel="stylesheet">
<style>
  :root {
    --sky: #12bdf2;
    --sky-deep: #0a9fd6;
    --band: rgba(9, 48, 72, 0.82);
    --slate: rgba(78, 80, 82, 0.9);
    --white: #ffffff;
    --ink: #4a4f55;
    --ink-soft: #7b8188;
    --accent: #11a9e6;
    --page: #eef0f2;
  }
  * { margin: 0; padding: 0; box-sizing: border-box; }
  html, body { width: 1200px; height: 838px; overflow: hidden; }
  body {
    background: var(--page);
    font-family: "Raleway", Arial, sans-serif;
    position: relative;
  }
  .spread {
    position: absolute;
    top: 238px;
    width: 560px;
    height: 362px;
    overflow: hidden;
  }
  .spread--outside { left: 27px; }
  .spread--inside { left: 613px; }
  .panel {
    position: absolute;
    top: 0;
    width: 280px;
    height: 362px;
    overflow: hidden;
  }
  .panel--left { left: 0; }
  .panel--right { left: 280px; }

  .art-blueprint {
    position: absolute; inset: 0;
    background: linear-gradient(160deg, #2cc7f5 0%, var(--sky) 45%, #0fb3ea 100%);
  }
  .art-house {
    position: absolute; inset: 0;
    background: linear-gradient(180deg, #2bb9ea 0%, var(--sky-deep) 60%, #1a8fc0 100%);
  }
  .art-interior {
    position: absolute; inset: 0;
    background: linear-gradient(180deg, #16b2ea 0%, #0a9bd6 55%, #0878b0 100%);
  }

  .band {
    position: absolute;
    left: 0;
    top: 220px;
    height: 26px;
    background: var(--band);
    display: flex;
    align-items: center;
    color: var(--white);
  }

  .brand-name {
    position: absolute;
    font-family: "Raleway", Arial, sans-serif;
    font-weight: 500;
    color: var(--white);
    white-space: nowrap;
    line-height: 1;
  }

  /* back cover */
  .back .brand-name { left: 19px; top: 166px; font-size: 15px; }
  .back .band { width: 280px; padding-left: 19px; gap: 26px; font-size: 9px; font-weight: 700; }
  .contact-item { display: flex; align-items: center; gap: 5px; }
  .contact-item svg { width: 7px; height: 7px; fill: var(--white); }
  .back .tagline {
    position: absolute; left: 19px; top: 251px;
    color: var(--white); font-size: 9px; font-weight: 400;
  }

  /* front cover */
  .front svg.cover-shape { position: absolute; inset: 0; }
  .front .brand-name { left: 100px; top: 158px; font-size: 20px; }
  .front .cover-tagline {
    position: absolute; left: 56px; top: 220px; height: 26px; width: 224px;
    display: flex; align-items: center;
    color: var(--white); font-size: 9.5px; font-weight: 400; letter-spacing: 3.6px;
  }
  .front .cover-url {
    position: absolute; left: 100px; top: 256px;
    color: var(--white); font-size: 9px; font-weight: 300;
  }

  /* inside */
  .inside-url {
    position: absolute; left: 152px; top: 24px;
    color: var(--white); font-size: 8px; font-weight: 300;
  }
  .inside .band { width: 340px; padding-left: 22px; font-size: 9.5px; font-weight: 600; }
  .services { display: flex; align-items: center; }
  .services .divider { width: 1px; height: 13px; background: var(--white); margin: 0 19px; }
  .inside .brand-name { left: 22px; top: 294px; font-size: 20px; }

  .inside svg.curve-shape { position: absolute; inset: 0; }

  .faq {
    position: absolute; left: 364px; top: 38px; width: 180px;
    color: var(--ink);
  }
  .faq-title { font-size: 11px; font-weight: 600; line-height: 1.15; }
  .faq-sub { font-size: 7.5px; font-weight: 600; color: var(--ink-soft); margin-top: 2px; }
  .steps {
    display: grid;
    grid-template-columns: 78px 78px;
    column-gap: 9px;
    row-gap: 14px;
    margin-top: 18px;
  }
  .step h3 { font-size: 4.6px; font-weight: 700; color: var(--accent); line-height: 1.3; }
  .step p { font-size: 4.4px; font-weight: 400; color: var(--ink-soft); line-height: 1.35; }
</style>
</head>
<body>

  <section class="spread spread--outside">
    <div class="panel panel--left back">
      <div class="art-blueprint" role="img" aria-label="Faint architectural blueprint drawing washed in sky blue"></div>
      <div class="brand-name">Q&amp;J Restoration</div>
      <div class="band">
        <span class="contact-item">
          <svg viewBox="0 0 10 8"><path d="M0 0h10v8H0z" fill="#fff"/><path d="M0.5 0.6L5 4.1 9.5 0.6" stroke="#093048" stroke-width="0.9" fill="none"/></svg>
          www.Q-J-Restoration.example
        </span>
        <span class="contact-item">
          <svg viewBox="0 0 10 10"><path d="M2.2 0.6l1.6 2.2-1 1.1c.6 1.3 1.6 2.3 2.9 2.9l1.1-1 2.2 1.6-.9 1.9C4.3 9.1.9 5.7.3 1.5z"/></svg>
          919.555.0147
        </span>
      </div>
      <p class="tagline">Insurance Claim Specialist</p>
    </div>

    <div class="panel panel--right front">
      <div class="art-house" role="img" aria-label="Photo of a house standing in flood water, tinted blue"></div>
      <svg class="cover-shape" viewBox="0 0 280 362" aria-hidden="true">
        <defs>
          <clipPath id="cover-arc"><path d="M113,0 A232,232 0 0 0 113,362 L280,362 L280,0 Z"/></clipPath>
        </defs>
        <g clip-path="url(#cover-arc)">
          <rect width="280" height="362" fill="var(--slate)"/>
          <rect y="220" width="280" height="26" fill="rgba(20,24,28,0.55)"/>
        </g>
      </svg>
      <div class="brand-name">Q&amp;J Restoration</div>
      <div class="cover-tagline">Insurance Claim Specialist</div>
      <p class="cover-url">www.Q-J-Restoration.example</p>
    </div>
  </section>

  <section class="spread spread--inside inside">
    <div class="art-interior" role="img" aria-label="Photo of a flooded modern kitchen interior, tinted blue"></div>
    <p class="inside-url">www.Q-J-Restoration.example</p>
    <div class="band">
      <div class="services">
        <span>COMMERCIAL</span><span class="divider"></span>
        <span>RESIDENTIAL</span><span class="divider"></span>
        <span>MOLD</span>
      </div>
    </div>
    <div class="brand-name">Q&amp;J Restoration</div>

    <svg class="curve-shape" viewBox="0 0 560 362">
      <defs>
        <clipPath id="inside-arc"><path d="M392,0 A232,232 0 0 0 392,362 L560,362 L560,0 Z"/></clipPath>
        <linearGradient id="homeowners" x1="0" y1="0" x2="1" y2="1">
          <stop offset="0" stop-color="#c9b59c"/>
          <stop offset="0.45" stop-color="#7d8a8c"/>
          <stop offset="1" stop-color="#3f6a8a"/>
        </linearGradient>
      </defs>
      <g clip-path="url(#inside-arc)">
        <rect width="560" height="220" fill="var(--white)"/>
        <rect y="220" width="560" height="142" fill="url(#homeowners)" role="img" aria-label="Photo of a happy couple sitting outside their restored modern home"/>
      </g>
    </svg>

    <div class="faq">
      <h2 class="faq-title">Water or Mold Damage?</h2>
      <p class="faq-sub">What happens after the cleanup?</p>
      <div class="steps">
        <div class="step">
          <h3>1. Adjuster’s Inspection</h3>
          <p>Feel Confident. Be sure you received a fair and accurate assessment &amp; repair of all damages with our team’s use of industry leading Estimating Systems and On-Site Review.</p>
        </div>
        <div class="step">
          <h3>2. Timely Settlement</h3>
          <p>Don’t wait. Minimize the hassle of long processing times from Estimate to Settlement when you team up with and Insurance Repair Specialist.</p>
        </div>
        <div class="step">
          <h3>3. Under One Roof</h3>
          <p>Don’t Worry. You won’t need to arrange meetings with multiple contractors; we’ll take care of everything from demo to final cleanup.</p>
        </div>
        <div class="step">
          <h3>4. Superior Craftsmanship</h3>
          <p>Don’t settle for satisfactory. Our team is committed to the highest standards of excellence every step of the way. Trust us when we say that we’ll make you smile.</p>
        </div>
      </div>
    </div>
  </section>

</body>
</html>
```